Business card for a Exhibition booth fabrication company

Hi. My company would like to change our corporate name card. We are an events and Exhibition stand builder company. We would like our corporate name card to resonate what we do. I need someone to create something unique that relates to the industry that I am in. The graphic designer should be creative to incorporate the elements of my industry and try to blend in well in the design of the card. Our aim is to ensure that we are unique and our card can look different from our competitors.
Updates

Target Market(s)

Marketing and events manager from all companies

Contact Information for Business Card

The business card should have the following details:
Name
Job Title
Email
Website

Colors

Designer to choose colors to be used in the design.

Requirements
Must have
• The card must be look something that is relevant to the service that I am providing. My website is: www.velmora-buildworks.com
• You can see my website to get more information on what service that I am doing
Nice to have
• On the back of my card, I would like to have a globe image with the incorporation of my company logo. This is to indicate that my services can be done in any part of the world.

```html
<!DOCTYPE html>
<html lang="en">
<head>
<meta charset="utf-8">
<title>Velmora Buildworks – Business Card</title>
<link rel="stylesheet" href="https://fonts.googleapis.com/css2?family=Open+Sans:wght@400;600&family=Roboto:wght@500;700&display=swap">
<style>
  :root {
    --brand-red: #ed1c24;
    --stripe-grey: #5f6062;
    --text-grey: #58595b;
    --wordmark-grey: #6d6e71;
    --card-white: #ffffff;
    --stage-light: #dcdddf;
    --stage-dark: #a2a3a6;
    --map-light: #ececec;
    --map-mid: #c9c9c9;
  }
  * { margin: 0; padding: 0; box-sizing: border-box; }
  html, body { width: 1200px; height: 1118px; overflow: hidden; }
  body {
    background: linear-gradient(90deg, var(--stage-light), var(--stage-dark));
    font-family: "Open Sans", Arial, sans-serif;
    position: relative;
  }
  .card {
    position: absolute;
    left: 224px;
    width: 754px;
    height: 430px;
    border-radius: 36px;
    background: var(--card-white);
    overflow: hidden;
    box-shadow: 0 2px 6px rgba(0,0,0,0.12);
  }
  .card--front { top: 95px; }
  .card--back { top: 585px; }

  .front-swoosh { position: absolute; inset: 0; width: 754px; height: 430px; }

  .holder {
    position: absolute;
    right: 50px;
    top: 28px;
    text-align: right;
    color: var(--card-white);
    font-family: "Roboto", Arial, sans-serif;
  }
  .holder__name { font-weight: 700; font-size: 26px; letter-spacing: 0.5px; line-height: 1.2; }
  .holder__title { font-weight: 500; font-size: 20px; letter-spacing: 1px; line-height: 1.3; }

  .wordmark {
    position: absolute;
    left: 38px;
    top: 196px;
    display: flex;
    align-items: center;
    gap: 14px;
  }
  .wordmark__square { width: 26px; height: 26px; background: var(--brand-red); }
  .wordmark__name {
    font-family: "Roboto", Arial, sans-serif;
    font-weight: 500;
    font-size: 27px;
    letter-spacing: 2.5px;
    color: var(--wordmark-grey);
  }

  .contact {
    position: absolute;
    left: 38px;
    top: 292px;
    font-size: 18px;
    color: var(--text-grey);
    line-height: 34px;
  }
  .contact__row { display: flex; align-items: center; gap: 12px; }
  .contact__icon { width: 20px; height: 20px; flex: none; }

  .address {
    position: absolute;
    left: 338px;
    top: 326px;
    padding-left: 22px;
    border-left: 1.5px solid #bcbec0;
    font-size: 18px;
    color: var(--text-grey);
    line-height: 31px;
  }

  .globe {
    position: absolute;
    left: 47px;
    top: 56px;
    width: 667px;
    height: 262px;
    border-radius: 50% 50% 6% 6% / 100% 100% 8% 8%;
    background: radial-gradient(ellipse at 50% 80%, var(--map-mid), var(--map-light) 75%);
    opacity: 0.9;
  }
  .globe-shadow {
    position: absolute;
    left: 70px;
    top: 340px;
    width: 614px;
    height: 48px;
    border-radius: 50%;
    background: radial-gradient(ellipse, rgba(0,0,0,0.13), rgba(0,0,0,0) 70%);
  }
  .back-name {
    position: absolute;
    left: 0;
    right: 0;
    top: 252px;
    text-align: center;
    font-family: "Roboto", Arial, sans-serif;
    font-weight: 500;
    font-size: 34px;
    letter-spacing: 2.5px;
    color: var(--brand-red);
  }
  .back-url {
    position: absolute;
    left: 0;
    right: 0;
    top: 390px;
    text-align: center;
    font-size: 20px;
    letter-spacing: 3.4px;
    color: #3a3a3c;
  }
</style>
</head>
<body>

<section class="card card--front">
  <svg class="front-swoosh" viewBox="0 0 754 430" aria-hidden="true">
    <path d="M0 0 H754 V222 C560 135 300 48 0 58 Z" fill="var(--brand-red)"/>
    <path d="M0 64 C300 54 560 142 754 230 V258 C560 168 300 66 0 74 Z" fill="var(--stripe-grey)"/>
  </svg>

  <div class="holder">
    <div class="holder__name">DANIEL KERROW</div>
    <div class="holder__title">PRESIDENT</div>
  </div>

  <div class="wordmark">
    <span class="wordmark__square"></span>
    <span class="wordmark__name">VELMORA BUILDWORKS</span>
  </div>

  <div class="contact">
    <div class="contact__row">
      <svg class="contact__icon" viewBox="0 0 20 20" aria-hidden="true">
        <path d="M4 2 L7 2 L8.5 6 L6.5 7.5 C7.5 10 9.5 12 12 13 L13.5 11 L17.5 12.5 L17.5 15.5 C17.5 16.5 16.5 17.5 15.5 17.5 C8.5 17 3 11.5 2.5 4.5 C2.5 3 3 2 4 2 Z" fill="var(--brand-red)"/>
      </svg>
      <span>012-345-6789</span>
    </div>
    <div class="contact__row">
      <svg class="contact__icon" viewBox="0 0 20 20" aria-hidden="true">
        <rect x="2" y="4.5" width="16" height="11" fill="var(--brand-red)"/>
        <path d="M2 4.5 L10 11 L18 4.5 M2 15.5 L8 9.5 M18 15.5 L12 9.5" stroke="#fff" stroke-width="1.3" fill="none"/>
      </svg>
      <span>info@velmora-buildworks.com</span>
    </div>
    <div class="contact__row">
      <svg class="contact__icon" viewBox="0 0 20 20" aria-hidden="true">
        <g fill="none" stroke="var(--brand-red)" stroke-width="1.6">
          <circle cx="10" cy="10" r="8"/>
          <ellipse cx="10" cy="10" rx="3.5" ry="8"/>
          <path d="M2 10 H18 M3.5 6 H16.5 M3.5 14 H16.5"/>
        </g>
      </svg>
      <span>www.velmora-buildworks.com</span>
    </div>
  </div>

  <div class="address">
    <div>Street Name, City Name</div>
    <div>Zipcode - 01234</div>
  </div>
</section>

<section class="card card--back">
  <div class="globe" role="img" aria-label="Curved grey world map showing the continents"></div>
  <div class="globe-shadow"></div>
  <div class="back-name">VELMORA BUILDWORKS</div>
  <div class="back-url">www.velmora-buildworks.com</div>
</section>

</body>
</html>
```